Harwick + Pell Architect Marketing campaign for a morern fresh architecture cutting egde firm th...

To create en exciting template for our monthly newsletters to go out to all our clients via email. I have added a bit of an idea of what we like but not limited to..... we like a nice clean fresh look with lots of white space. I hve aslo added a sketch of the type of how we might layt it out - you may have a better idea. also the pics of the projects for the first issue (issue #1)We like the opening page like the attached brewlane had and replace the cup with apic of our building/office. Cant wait to see what you come up with.

Target Market(s)

young professionals

Industry/Entity Type

Architectural

Font styles to use
Serif

Colors

Designer to choose colors to be used in the design.

Requirements
Must have
• Logo, text information provided, photos provided
Nice to have
• lots of white space, clean and frest looking

```html
<!DOCTYPE html>
<html lang="en">
<head>
<meta charset="utf-8">
<title>Harwick + Pell Architecture — Newsletter Issue #1</title>
<link href="https://fonts.googleapis.com/css2?family=Poppins:wght@600;700&family=Source+Sans+3:wght@400;600;700&display=swap" rel="stylesheet">
<style>
:root{
  --green:#5fb24b;
  --ink:#333333;
  --body:#3d3d3d;
  --white:#ffffff;
  --navy:#17305a;
  --brand-ink:#1a1a1a;
  --head:'Poppins',sans-serif;
  --text:'Source Sans 3',sans-serif;
}
*{margin:0;padding:0;box-sizing:border-box}
html,body{width:1200px;height:5398px;overflow:hidden;background:var(--white)}
body{position:relative;font-family:var(--text);color:var(--body)}
section,header,footer{position:absolute;left:0;width:1200px}
.abs{position:absolute}

/* header */
.masthead{top:0;height:185px;background:var(--white)}
.brand{left:0;width:1200px;top:70px;display:flex;justify-content:center;align-items:center;gap:12px}
.brand-square{display:block;width:26px;height:26px;background:var(--brand-ink)}
.brand-name{font-family:var(--text);font-weight:700;font-size:30px;color:var(--brand-ink)}

/* hero */
.hero{top:185px;height:495px}
.hero-photo{position:absolute;inset:0;background:linear-gradient(100deg,#2a2f38 0%,#3b3f46 40%,#23262c 70%,#121418 100%)}
.hero-photo::after{content:"";position:absolute;inset:0;background:linear-gradient(180deg,rgba(0,0,0,.15),rgba(0,0,0,.35) 60%,rgba(60,45,30,.5))}
.hero h1{position:absolute;left:83px;top:125px;font-family:var(--head);font-weight:700;font-size:54px;color:var(--white);letter-spacing:-.5px;z-index:1}
.hero p{position:absolute;left:83px;top:228px;width:700px;font-size:25px;line-height:51px;color:var(--white);z-index:1}

/* welcome */
.welcome{top:680px;height:652px;text-align:center}
.welcome h2{position:absolute;left:0;width:1200px;top:108px;font-family:var(--head);font-weight:700;font-size:46px;color:var(--ink)}
.welcome p{position:absolute;left:95px;width:1010px;font-size:26px;line-height:50px;color:var(--body)}
.welcome .p1{top:242px;left:100px;width:1000px}
.welcome .p2{top:450px;left:60px;width:1080px}

/* green panels */
.panel{background:var(--green);color:var(--white)}
.panel .bg{position:absolute;inset:0;background:linear-gradient(180deg,rgba(255,255,255,.05),rgba(0,0,0,.04) 60%,rgba(255,255,255,.06))}
.panel h2{position:absolute;font-family:var(--head);font-weight:700;font-size:48px;letter-spacing:-.5px}
.panel h3{position:absolute;font-family:var(--text);font-weight:700;font-size:30px;line-height:55px;text-transform:uppercase}
.panel p{position:absolute;width:546px;font-size:27px;line-height:55px;text-align:justify;hyphens:auto}

.photo{position:absolute;width:421px;height:277px}
.photo::after{content:"";position:absolute;left:20px;top:12px;right:20px;bottom:12px;border:3px solid var(--white)}
.sky-a{background:linear-gradient(180deg,#2f7fd9 0%,#7bb4ea 45%,#c9cdd3 70%,#8e9399 100%)}
.sky-b{background:linear-gradient(180deg,#5a5e86 0%,#9d9bb8 45%,#4a4d5c 75%,#23252d 100%)}
.sky-c{background:linear-gradient(180deg,#3d8ce0 0%,#9cc6ee 40%,#7b8a95 70%,#c9c4b8 100%)}
.sky-d{background:linear-gradient(180deg,#2a76d6 0%,#6ea8e6 40%,#5c7a9a 65%,#6ea04a 100%)}
.sky-e{background:linear-gradient(100deg,#8a2e22 0%,#a34232 40%,#6d8fb0 65%,#9fc2e2 100%)}

.drawing{top:1332px;height:940px}
.drawing h2{left:77px;top:125px}
.drawing h3{left:82px;top:202px}
.drawing p{left:86px;top:302px}

/* under construction */
.construction{top:2272px;height:1268px}
.construction h2{position:absolute;left:520px;top:111px;font-family:var(--head);font-weight:700;font-size:48px;color:#222;letter-spacing:-.5px}
.construction h3{position:absolute;left:525px;top:190px;font-family:var(--text);font-weight:700;font-size:28px;color:#222}
.construction p{position:absolute;left:538px;top:272px;width:528px;font-size:27px;line-height:55px;text-align:justify;hyphens:auto;color:var(--body)}
.construction .photo{width:392px;height:258px}
.construction .photo::after{left:4px;top:4px;right:4px;bottom:4px;border-width:2px}

/* feature */
.feature{top:3540px;height:1145px}
.feature h2{left:83px;top:135px}
.feature h3{left:77px;top:208px;font-size:28px}
.feature p{left:84px;top:355px;width:548px}

/* social */
.social{top:4685px;height:655px;text-align:center}
.social .bg{position:absolute;inset:0;background:linear-gradient(180deg,#ffffff 0%,#f3f4f6 55%,#e9ebee 100%)}
.social h2{position:absolute;left:0;width:1200px;top:98px;font-family:var(--head);font-weight:700;font-size:48px;color:#222;letter-spacing:-.5px}
.social p{position:absolute;left:150px;width:900px;top:193px;font-size:26px;line-height:55px;color:var(--body)}
.channels{position:absolute;left:0;width:1200px;top:352px;display:flex;justify-content:center;gap:34px}
.channel{font-family:var(--text);font-weight:700;font-size:22px;color:#1a1a1a;display:flex;align-items:center;gap:8px}
.channel i{display:block;width:16px;height:16px;background:#1a1a1a}
.badge{position:absolute;top:438px}
.badge-a{left:263px;width:245px;height:170px;border-radius:6px;background:#555}
.badge-b{left:676px;width:198px;height:70px;top:470px;border-radius:4px;background:#1e3a7a}

/* footer */
.footer{top:5340px;height:58px;background:var(--navy);color:var(--white);font-size:21px}
.footer .legal{position:absolute;left:83px;top:15px}
.footer .code{position:absolute;left:1060px;top:15px}
</style>
</head>
<body>

<header class="masthead">
  <div class="abs brand">
    <span class="brand-square"></span>
    <span class="brand-name">Harwick + Pell</span>
  </div>
</header>

<section class="hero">
  <div class="hero-photo" role="img" aria-label="Dusk photograph of the studio's modern dark-clad office building with lit entrance"></div>
  <h1>We’re glad you’re here</h1>
  <p>Now that you are a Harwick + Pell Architecture insider you’ll be among the first to hear about upcoming projects that the studio is working on, completed projects, news and more.</p>
</section>

<section class="welcome">
  <h2>WELCOME</h2>
  <p class="p1">It appears that there are a lot of people are genuinely interested in the building and construction industry, and we here at Harwick + Pell Architecture often get asked “what we are up to” and “what cool projects have we got on the go”. With that being said we thought we would share</p>
  <p class="p2">We plan on keeping you all up to date on what the studio is up to with monthly newsletters</p>
</section>

<section class="panel drawing">
  <div class="bg"></div>
  <h2>ON THE DRAWING BOARD</h2>
  <h3>LAKE MARROW HOUSE // RESIDENTIAL</h3>
  <p>We have recently completed this two story house concept overlooking the canals at Lake Marrow here in Ashford Vale. We are currently in the Working Drawing phase at present. This house will stand out from the crowd and has a mixture of cedar, standing seam wall cladding and pre-cast concrete panels. We are really excited to see this project to progress to construction. We will keep you posted on this one!!</p>
  <div class="photo sky-a" style="left:692px;top:249px" role="img" aria-label="White multi-storey building with balconies under a blue sky"></div>
  <div class="photo sky-b" style="left:692px;top:591px" role="img" aria-label="Low dark building lit at dusk under a cloudy purple sky"></div>
</section>

<section class="construction">
  <h2>UNDER CONSTRUCTION</h2>
  <h3>MERRIN STREET – STAGE 1 // COMMERCIAL</h3>
  <div class="photo sky-c" style="left:79px;top:189px" role="img" aria-label="Glass office tower beside a tree-lined walkway"></div>
  <div class="photo sky-d" style="left:79px;top:506px" role="img" aria-label="Colourful apartment blocks behind a row of trees"></div>
  <p>This new development currently being construction by Dunmore Commercial in Kelbridge is the anchor development for Merrin Street and the beginning of the reconfiguration / upgrade of the Kelbridge Town Centre. This is part of a major redevelopment for Kelbridge. We have worked closely with the Kelbridge District Council and surrounding residential neighbours so that new development benefits all involved. The building is fully tenanted with Monotone Coffee, Lantern Bowl Noodle House, Spice Route Kitchen, Cellar Corner, Thread &amp; Co Clothing Store and a small dairy. Tenants are currently completing fit-outs for the spaces and the project is fast nearing completion and will be open for business in the next few months.</p>
</section>

<section class="panel feature">
  <div class="bg"></div>
  <h2>FEATURE PROJECT</h2>
  <h3>IRONLINE CUTTING &amp; PROCESSING LTD<br>&nbsp;COMMERCIAL</h3>
  <p>This new office and factory located in the new Ashford Vale Business Park is comprised of a large Cutting and Processing facility for the manufacturer of steel plate profiles. The facility 1,500m² houses two 10-tonne gantry cranes running the full length of the 60 x 25 metre workshop and was designed with the emphasis on maximum plate storage and profile cutting efficiency. Alongside the processing facility is an attached 238m² modern single level office building has been designed to project the character and brand of Ironline Cutting and to sit within the context of the Business Park. The interior fit-out</p>
  <div class="photo sky-e" style="left:692px;top:250px" role="img" aria-label="Office facade with red vertical fins and glass curtain wall"></div>
  <div class="photo sky-a" style="left:692px;top:595px" role="img" aria-label="White multi-storey building with balconies under a blue sky"></div>
</section>

<section class="social">
  <div class="bg" role="img" aria-label="Faint city skyline backdrop"></div>
  <h2>STAY CONNECTION WITH US</h2>
  <p>Also remember to follow us on our social media platforms where are keeping our followers up to date</p>
  <div class="channels">
    <span class="channel"><i></i>Friendly</span>
    <span class="channel"><i></i>Linkup</span>
    <span class="channel"><i></i>Houseboard</span>
  </div>
  <div class="badge badge-a" role="img" aria-label="Professional membership badge"></div>
  <div class="badge badge-b" role="img" aria-label="Industry association badge"></div>
</section>

<footer class="footer">
  <span class="legal">© 2019 All Rights Reserved | Privacy Policy | Terms and Conditions</span>
  <span class="code">C36</span>
</footer>

</body>
</html>
```